Pinecrest Harbor Foundation Web Design

The design we need is for a WordPress blog that will be our content platform. We are a registered 501(c)3 non-profit that focuses on financially supporting the treatment of cancer patients that have been told they have no hope and there is nothing the conventional medical system can do for them. Through this wesbite we want to both rasie awareness about the treatment options plus, raise funds for treating patients. The two primary target audiences of the site are...

1. Terminally ill patients and their families to let them know that there is an option other then hospice and that we are hear to support that option.

2. People looking to help donate to a worthwhile cause that resonates with them.

The website is https://pinecrestharborfoundation.org/

See attached logo designs!!!

Target Market(s)

Cancer patients and their families

Industry/Entity Type

Foundation

Font styles to use
Sans Serif

Colors
ffffff
fbed22

Requirements
Must have
• I like this look of this site. It is clean, simple, helpful, soft. I like the flow of the pages.
• http://www.meadowsforcalm.org/
• I like the design and flow but NOT the color or boldness
• https://tvbn-youth.org/
• I like this style for a donation page.
• https://www.tumorstudyhub.org/we-are-tsh/join-the-cause/donations/one-time-donation
• with the addition of a Would you like your employer to match? button.
Nice to have
• White black and gold - but soft
• Even possibly grayscale like the site I like.

```html
<!DOCTYPE html>
<html lang="en">
<head>
<meta charset="utf-8">
<title>Pinecrest Harbor Foundation</title>
<link href="https://fonts.googleapis.com/css2?family=Lato:wght@400;700;900&family=Montserrat:wght@500;600&family=Oswald:wght@500&display=swap" rel="stylesheet">
<style>
:root{
  --gold:#ebc85a;
  --gold-soft:#f0d57f;
  --ink:#262626;
  --band:#5a5a5a;
  --text:#333333;
  --muted:#8a8a8a;
  --mist:#f0f0f0;
  --white:#ffffff;
}
*{box-sizing:border-box;margin:0;padding:0}
html,body{width:1200px;height:3158px;overflow:hidden}
body{font-family:"Lato",Arial,sans-serif;color:var(--text);background:var(--white);position:relative}
.section{position:absolute;left:0;width:1200px}
.center{text-align:center}
.rule{width:120px;height:2px;background:var(--text);margin:20px auto 0}

/* header */
.site-header{top:0;height:126px;background:var(--white)}
.brand{position:absolute;left:99px;top:36px;display:flex;align-items:center;gap:12px}
.brand-mark{width:34px;height:34px;background:var(--gold)}
.brand-name{font-family:"Lato",sans-serif;font-weight:900;font-size:17px;line-height:20px;color:var(--ink);letter-spacing:.5px}
.contact{position:absolute;right:99px;top:22px;display:flex;align-items:center;gap:14px;font-size:15px}
.contact .dot{width:30px;height:30px;border-radius:50%;display:inline-flex;align-items:center;justify-content:center}
.contact .email{color:var(--gold);display:flex;align-items:center;gap:10px}
.contact .phone{display:flex;align-items:center;gap:10px;color:var(--text);margin-left:10px}
.social-top{display:flex;gap:6px;margin-left:14px}
.social-top span{width:22px;height:22px;background:#9b9b9b}
.main-nav{position:absolute;right:99px;top:80px;display:flex;gap:60px;font-family:"Montserrat",sans-serif;font-weight:500;font-size:15px;color:var(--ink)}

/* hero */
.hero{top:126px;height:514px;background:linear-gradient(90deg,#6d6a68 0%,#8c8682 45%,#c9c2bd 70%,#b6aaa2 100%)}
.hero-title{position:absolute;left:99px;top:150px;font-family:"Oswald",sans-serif;font-weight:500;font-size:56px;color:var(--white);letter-spacing:-.5px}
.hero-text{position:absolute;left:99px;top:240px;width:485px;font-size:15px;line-height:22px;color:var(--white);font-weight:700}
.btn-outline{position:absolute;left:99px;top:320px;width:120px;height:51px;border:2px solid var(--white);color:var(--white);font-size:15px;display:flex;align-items:center;justify-content:center}
.arrow{position:absolute;top:240px}

/* features */
.features{top:640px;height:434px;background:var(--band)}
.feature{position:absolute;top:50px;width:240px;text-align:center;color:var(--white)}
.feature svg{display:block;margin:0 auto}
.feature h3{font-family:"Montserrat",sans-serif;font-weight:600;font-size:23px;margin-top:26px}
.feature p{font-size:14px;line-height:25px;margin-top:12px;font-weight:700}
.curve{position:absolute;left:0;bottom:0}

/* about */
.about{top:1074px;height:391px}
.about h2{font-family:"Lato",sans-serif;font-weight:700;font-size:28px;color:#444;margin-top:-22px}
.about p{width:1000px;margin:36px auto 0;font-size:14px;line-height:27px;color:var(--muted)}
.about p + p{margin-top:18px}
.btn-gold{display:flex;align-items:center;justify-content:center;width:130px;height:49px;background:var(--gold);font-weight:700;font-size:15px;color:var(--ink);margin:40px auto 0}

/* awareness */
.awareness{top:1465px;height:539px;background:var(--mist)}
.awareness h2,.news h2{font-weight:700;font-size:28px;color:var(--ink);padding-top:62px}
.card{position:absolute;top:179px;width:484px;height:267px;display:flex}
.card-body{width:238px;padding:24px 22px;text-align:center}
.card-body h3{font-weight:700;font-size:20px;line-height:26px}
.card-body p{font-size:14px;line-height:21px;margin-top:10px}
.card-body .btn-sm{display:inline-block;margin-top:18px;border:2px solid currentColor;padding:8px 12px;font-size:13px;font-weight:700}
.card-photo{flex:1}
.card.light .card-body{background:var(--gold);color:var(--ink)}
.card.dark .card-body{background:var(--ink);color:var(--white)}

/* news */
.news{top:2004px;height:598px}
.news-item{position:absolute;top:181px;width:250px;text-align:center}
.news-photo{width:238px;height:238px;border-radius:50%;margin:0 auto;position:relative}
.date{position:absolute;right:0;bottom:2px;width:60px;height:60px;border-radius:50%;display:flex;flex-direction:column;align-items:center;justify-content:center;font-weight:700;font-size:14px;line-height:16px}
.date.dark{background:var(--ink);color:var(--white)}
.date.gold{background:var(--gold);color:var(--ink)}
.news-item p{font-size:15px;line-height:23px;margin-top:20px;color:var(--ink)}

/* newsletter */
.newsletter{top:2602px;height:84px;background:var(--gold);display:flex;align-items:center;padding:0 99px}
.newsletter label{font-family:"Montserrat",sans-serif;font-weight:600;font-size:22px;color:var(--ink);margin-right:12px}
.newsletter .field{width:664px;height:44px;border:2px solid var(--ink);background:var(--gold-soft);font-size:14px;display:flex;align-items:center;padding-left:14px;color:var(--ink)}
.newsletter .submit{margin-left:auto;width:168px;height:44px;background:var(--ink);color:var(--white);font-weight:700;font-size:16px;display:flex;align-items:center;justify-content:center}

/* footer */
.site-footer{top:2686px;height:472px;background:var(--ink);color:var(--white)}
.footer-brand{position:absolute;left:0;width:1200px;top:82px;font-weight:900;font-size:24px;line-height:30px;letter-spacing:1px;text-align:center}
.footer-social{position:absolute;top:227px;left:0;width:1200px;display:flex;justify-content:center;gap:10px}
.footer-social span{width:42px;height:42px;border:2px solid var(--white);border-radius:50%}
.footer-nav{position:absolute;top:316px;left:0;width:1200px;display:flex;justify-content:center;gap:26px;font-family:"Montserrat",sans-serif;font-weight:600;font-size:15px}
.footer-line{position:absolute;top:387px;left:99px;width:1002px;height:1px;background:var(--white)}
.copyright{position:absolute;top:420px;left:0;width:1200px;text-align:center;font-size:14px;font-weight:700}
</style>
</head>
<body>

<header class="section site-header">
  <div class="brand"><span class="brand-mark"></span><span class="brand-name">PINECREST HARBOR<br>FOUNDATION</span></div>
  <div class="contact">
    <span class="email"><span class="dot" style="background:var(--gold)"><svg width="14" height="10" viewBox="0 0 14 10"><rect x="0.5" y="0.5" width="13" height="9" fill="none" stroke="#fff"/><path d="M0.5 0.5L7 6L13.5 0.5" fill="none" stroke="#fff"/></svg></span>info@pinecrestharborfoundation.org</span>
    <span class="phone"><span class="dot" style="background:#555"><svg width="14" height="14" viewBox="0 0 14 14"><path d="M3 1l2 3-1.5 1.5a8 8 0 0 0 5 5L10 9l3 2-1 2c-6 0-11-5-11-11z" fill="#fff"/></svg></span>180 555 0148</span>
    <span class="social-top"><span></span><span></span><span></span><span></span><span></span></span>
  </div>
  <nav class="main-nav"><span>HOME</span><span>ABOUT US</span><span>CHARITY</span><span>SPONSORSHIP</span><span>TREATMENT</span><span>CONTACT US</span></nav>
</header>

<section class="section hero" role="img" aria-label="Smiling doctor in a white coat talking with a patient">
  <h1 class="hero-title">Pinecrest Harbor Foundation</h1>
  <p class="hero-text">Sed ut perspiciatis unde omnis iste natus error sit voluptatem accusantium doloremque laudantium.</p>
  <span class="btn-outline">Read More</span>
  <svg class="arrow" style="left:36px" width="20" height="40" viewBox="0 0 20 40"><path d="M18 2L2 20L18 38" fill="none" stroke="#fff" stroke-width="2"/></svg>
  <svg class="arrow" style="right:36px" width="20" height="40" viewBox="0 0 20 40"><path d="M2 2L18 20L2 38" fill="none" stroke="#fff" stroke-width="2"/></svg>
</section>

<section class="section features">
  <div class="feature" style="left:82px">
    <svg width="80" height="70" viewBox="0 0 80 70"><path d="M40 38C26 28 22 22 22 16a8 8 0 0 1 18-4a8 8 0 0 1 18 4c0 6-4 12-18 22z" fill="none" stroke="#fff" stroke-width="4"/><path d="M6 52h18l16 6h28v6H38L22 60H6z" fill="#fff"/></svg>
    <h3>Charities</h3><p>Morbi diam mauris viverra in<br>gravida eu matti</p>
  </div>
  <div class="feature" style="left:343px">
    <svg width="80" height="70" viewBox="0 0 80 70"><circle cx="30" cy="14" r="9" fill="#fff"/><circle cx="50" cy="14" r="9" fill="#fff"/><path d="M14 60c0-22 10-34 26-34s26 12 26 34z" fill="#fff"/></svg>
    <h3>Organisation</h3><p>Morbi diam mauris viverra in<br>gravida eu matti</p>
  </div>
  <div class="feature" style="left:621px">
    <svg width="80" height="70" viewBox="0 0 80 70"><rect x="26" y="6" width="40" height="22" fill="#fff" transform="rotate(-12 46 17)"/><path d="M6 46h18l16 6h28v6H38L22 54H6z" fill="#fff"/></svg>
    <h3>Sponsorship</h3><p>Morbi diam mauris viverra in<br>gravida eu matti</p>
  </div>
  <div class="feature" style="left:874px">
    <svg width="80" height="70" viewBox="0 0 80 70"><path d="M40 20c-10-14-32-10-30 8c2 14 18 24 30 38c12-14 28-24 30-38c2-18-20-22-30-8z" fill="#fff"/><path d="M40 22v40" stroke="#5a5a5a" stroke-width="4"/></svg>
    <h3>Treatments</h3><p>Morbi diam mauris viverra in<br>gravida eu matti</p>
  </div>
  <svg class="curve" width="1200" height="140" viewBox="0 0 1200 140">
    <path d="M0 140V115Q600 -30 1200 90V140Z" fill="#262626"/>
    <path d="M0 140V135Q600 0 1200 112V140Z" fill="#ffffff"/>
    <circle cx="600" cy="50" r="44" fill="#ffffff"/>
  </svg>
</section>

<section class="section about center">
  <h2>About Pinecrest Harbor Foundation</h2>
  <div class="rule"></div>
  <p>Nemo enim ipsam voluptatem quia voluptas sit aspernatur aut odit aut fugit, sed quia consequuntur magni dolores eos qui ratione voluptatem sequi nesciunt. Neque porro quisquam est, qui dolorem ipsum quia dolor sit amet, consectetur, adipisci velit, sed quia non numquam eius modi tempora incidunt ut labore et dolore magnam aliquam quaerat voluptatem.</p>
  <p>Sed ut perspiciatis unde omnis iste natus error sit voluptatem accusantium doloremque laudantium, totam rem aperiam, eaque ipsa quae ab illo inventore veritatis et quasi architecto beatae vitae dicta sunt explicabo.</p>
  <span class="btn-gold">READ MORE</span>
</section>

<section class="section awareness center">
  <h2>Raise Awareness</h2>
  <div class="rule"></div>
  <article class="card light" style="left:101px">
    <div class="card-body"><h3>Treatment Options Plus</h3><p>Lorem ipsum dolor sit amet, consectetur adipiscing elit. Aliquam pulvinar eleentum vestibulum. Quisque nec dignissim.</p><span class="btn-sm">MORE DETAILS</span></div>
    <div class="card-photo" role="img" aria-label="Nurse caring for an elderly patient in bed" style="background:linear-gradient(135deg,#9fb6c8,#d9d4cf)"></div>
  </article>
  <article class="card dark" style="left:617px">
    <div class="card-body"><h3>Raise Funds For Treating Patients</h3><p>Lorem ipsum dolor sit amet, consectetur adipiscing elit. Aliquam pulvinar eleentum vestibulum. Quisque nec dignissim.</p><span class="btn-sm">MORE DETAILS</span></div>
    <div class="card-photo" role="img" aria-label="Senior man with a doctor in a clinic" style="background:linear-gradient(135deg,#b9a89a,#e4e0da)"></div>
  </article>
</section>

<section class="section news center">
  <h2>Latest News</h2>
  <div class="rule"></div>
  <div class="news-item" style="left:100px">
    <div class="news-photo" role="img" aria-label="Hands holding in comfort" style="background:linear-gradient(135deg,#8a4a3a,#c98f78)"><span class="date dark">MAR<br>10</span></div>
    <p>Duis aute irure dolor in reprehenderit in voluptate velit esse cillum.</p>
  </div>
  <div class="news-item" style="left:351px">
    <div class="news-photo" role="img" aria-label="Doctor wearing an awareness ribbon" style="background:linear-gradient(135deg,#cdbfb4,#f1ece8)"><span class="date gold">APR<br>10</span></div>
    <p>Duis aute irure dolor in reprehenderit in voluptate velit esse cillum.</p>
  </div>
  <div class="news-item" style="left:601px">
    <div class="news-photo" role="img" aria-label="Medical staff attending a patient" style="background:linear-gradient(135deg,#7fa8b8,#d8d2c8)"><span class="date dark">JAN<br>10</span></div>
    <p>Duis aute irure dolor in reprehenderit in voluptate velit esse cillum.</p>
  </div>
  <div class="news-item" style="left:850px">
    <div class="news-photo" role="img" aria-label="Doctor with a smiling senior patient" style="background:linear-gradient(135deg,#d5cbc2,#8e7a66)"><span class="date gold">MAR<br>10</span></div>
    <p>Duis aute irure dolor in reprehenderit in voluptate velit esse cillum.</p>
  </div>
</section>

<section class="section newsletter">
  <label>NEWSLETTER:</label>
  <span class="field">Email Address</span>
  <span class="submit">SUBMIT</span>
</section>

<footer class="section site-footer">
  <div class="footer-brand">PINECREST HARBOR<br>FOUNDATION</div>
  <div class="footer-social"><span></span><span></span><span></span><span></span><span></span></div>
  <nav class="footer-nav"><span>HOME</span><span>|</span><span>ABOUT US</span><span>|</span><span>CHARITY</span><span>|</span><span>SPONSORSHIP</span><span>|</span><span>TREATMENT</span><span>|</span><span>CONTACT US</span></nav>
  <div class="footer-line"></div>
  <p class="copyright">Copyright © 2017 Pinecrest Harbor Foundation. All Right Reserved</p>
</footer>

</body>
</html>
```